Freelancer Information Security professional needs a business card

I need a simple, young, elegant business card. I'm a freelancer in the InfoSec area and want to be able to give my card to potential customers and new people I meet.

I'd like to have a clean, professional look but at same time not boring or corporate.

The only requirement is to have my "introduction" phrase which is:
"Half hacker, half mercenary."

I have added a card I have as a example, which I think it gives a good example of style I want.

Target Market(s)

Technology / Computers / Engineering

Industry/Entity Type

Information Technology

Contact Information for Business Card

Contact fields I want included:

(351) 93 618 20 54
tomas@vendoza.im
https://vendoza.im

Font styles to use
Sans Serif

Requirements
Nice to have
• Card doesn't need to have a doubled side, but it looks good / fits the design then please do include.
Should not have
• Outdated graphics or images; too much patterns/colors.

```html
<!DOCTYPE html>
<html lang="en">
<head>
<meta charset="utf-8">
<title>Tomas Vendoza — Business Card</title>
<link rel="stylesheet" href="https://fonts.googleapis.com/css2?family=Roboto+Condensed:wght@300;400;700&family=Abel&display=swap">
<style>
  :root {
    --brand-blue: #00b4e6;
    --brand-green: #8dc63f;
    --tint-blue: #d6f1fb;
    --tint-green: #e6f3d3;
    --ink: #333333;
    --paper: #ffffff;
    --backdrop: #e9e6e1;
  }
  html, body {
    margin: 0;
    padding: 0;
    width: 1200px;
    height: 952px;
    overflow: hidden;
    background: var(--backdrop);
  }
  .card {
    position: absolute;
    left: 137px;
    top: 201px;
    width: 914px;
    height: 540px;
    background: var(--paper);
    overflow: hidden;
    box-shadow: 0 2px 8px rgba(0,0,0,0.12);
  }
  .card__band {
    position: absolute;
    left: 0;
    bottom: 0;
    width: 100%;
    height: 63px;
    background: var(--brand-blue);
  }
  .card__accent {
    position: absolute;
    left: 712px;
    top: 150px;
    width: 202px;
    height: 327px;
    background: linear-gradient(160deg, var(--tint-blue), var(--tint-green));
  }
  .card__mark {
    position: absolute;
    left: 150px;
    top: 108px;
    width: 70px;
    height: 70px;
    border-radius: 50%;
    background: var(--brand-blue);
  }
  .identity {
    position: absolute;
    left: 257px;
    top: 124px;
    font-family: "Roboto Condensed", sans-serif;
  }
  .identity__name {
    margin: 0;
    font-size: 40px;
    font-weight: 700;
    letter-spacing: 1px;
    line-height: 46px;
    color: var(--brand-blue);
  }
  .identity__name .surname { color: var(--brand-green); }
  .identity__tagline {
    margin: 0;
    font-size: 29px;
    font-weight: 300;
    line-height: 36px;
    color: var(--brand-blue);
    text-transform: uppercase;
  }
  .contacts {
    position: absolute;
    left: 264px;
    top: 257px;
    margin: 0;
    padding: 0;
    list-style: none;
    font-family: "Abel", sans-serif;
    font-size: 32px;
    letter-spacing: 0.5px;
    color: var(--ink);
  }
  .contacts__item {
    display: flex;
    align-items: center;
    height: 44px;
    margin-bottom: 28px;
  }
  .contacts__icon {
    width: 36px;
    height: 36px;
    margin-right: 39px;
    flex: none;
  }
</style>
</head>
<body>
  <main class="card">
    <div class="card__band"></div>
    <div class="card__accent" role="img" aria-label="Decorative circuit-line accent in blue and green"></div>

    <div class="card__mark"></div>

    <header class="identity">
      <h1 class="identity__name">TOMAS <span class="surname">VENDOZA</span></h1>
      <p class="identity__tagline">Half hacker, half mercenary.</p>
    </header>

    <ul class="contacts">
      <li class="contacts__item">
        <svg class="contacts__icon" viewBox="0 0 36 36" aria-hidden="true">
          <rect x="10" y="4" width="17" height="28" rx="3" fill="none" stroke="var(--brand-blue)" stroke-width="2.2"/>
          <line x1="13" y1="9" x2="24" y2="9" stroke="var(--brand-blue)" stroke-width="1.6"/>
          <line x1="13" y1="26" x2="24" y2="26" stroke="var(--brand-blue)" stroke-width="1.6"/>
          <circle cx="18.5" cy="29" r="1.2" fill="var(--brand-blue)"/>
        </svg>
        <span>(351) 93 618 20 54</span>
      </li>
      <li class="contacts__item">
        <svg class="contacts__icon" viewBox="0 0 36 36" aria-hidden="true">
          <rect x="3" y="9" width="30" height="19" fill="none" stroke="var(--brand-green)" stroke-width="2.2"/>
          <polyline points="3,9 18,21 33,9" fill="none" stroke="var(--brand-green)" stroke-width="2.2"/>
          <line x1="3" y1="28" x2="14" y2="18" stroke="var(--brand-green)" stroke-width="1.6"/>
          <line x1="33" y1="28" x2="22" y2="18" stroke="var(--brand-green)" stroke-width="1.6"/>
        </svg>
        <span>tomas@vendoza.im</span>
      </li>
      <li class="contacts__item">
        <svg class="contacts__icon" viewBox="0 0 36 36" aria-hidden="true">
          <g fill="none" stroke="var(--brand-blue)" stroke-width="1.8">
            <circle cx="18" cy="18" r="15"/>
            <ellipse cx="18" cy="18" rx="7" ry="15"/>
            <line x1="18" y1="3" x2="18" y2="33"/>
            <line x1="3" y1="18" x2="33" y2="18"/>
            <path d="M6 10 H30 M6 26 H30"/>
          </g>
        </svg>
        <span>https://vendoza.im</span>
      </li>
    </ul>
  </main>
</body>
</html>
```